Jolly Paws Business Card Update

I have a business card which I love. I want to keep the same logo, colours, font and style. I want to upgrade the scripting and remove some elements and add others.
On the front side under Services - remove the existing wording and insert - Providing individual coaching strategies to create happy, healthy and social canine companions
Under Denise Carvell amend the current wording to read: Qualified in Dog Behavioural Training, Natural Animal Healthcare and Animal Health Science
On the reverse side to remove the web address.

```html
<!DOCTYPE html>
<html lang="en">
<head>
<meta charset="utf-8">
<title>Jolly Paws Business Card</title>
<link href="https://fonts.googleapis.com/css2?family=Open+Sans:ital,wght@0,400;0,600;0,700;1,400&family=Arimo:wght@400&display=swap" rel="stylesheet">
<style>
  :root {
    --bg: #2a2a2a;
    --blue-deep: #233c8c;
    --blue-mid: #1f66b8;
    --blue-light: #0a8fd1;
    --red-dark: #6a181a;
    --red: #cf171e;
    --red-mid: #8e1c20;
    --cream: #efe8d2;
    --cream-dark: #c9bd98;
    --ring: #b41d22;
    --white: #ffffff;
    --navy-text: #1b2a55;
  }
  * { margin: 0; padding: 0; box-sizing: border-box; }
  html, body { width: 1200px; height: 1138px; overflow: hidden; }
  body { background: var(--bg); font-family: "Open Sans", sans-serif; color: var(--white); position: relative; }

  .card {
    position: absolute;
    border-radius: 14px;
    overflow: hidden;
    background: linear-gradient(20deg, var(--blue-deep) 0%, var(--blue-mid) 50%, var(--blue-light) 100%);
    box-shadow: 0 4px 10px rgba(0,0,0,0.45);
  }
  .card--front { left: 274px; top: 186px; width: 623px; height: 376px; }
  .card--back  { left: 276px; top: 608px; width: 618px; height: 374px; }

  .brand-disc {
    position: absolute;
    border-radius: 50%;
    background: radial-gradient(circle, var(--cream) 55%, var(--cream-dark) 100%);
    border: 6px solid var(--ring);
  }
  .card--front .brand-disc { left: 237px; top: 35px; width: 150px; height: 150px; }
  .card--back .brand-disc  { left: 33px; top: 39px; width: 114px; height: 114px; border-width: 5px; }

  .brand-name { position: absolute; font-family: "Open Sans", sans-serif; font-weight: 600; color: var(--white); letter-spacing: 1px; white-space: nowrap; line-height: 1; }
  .card--front .brand-name { left: 0; width: 100%; text-align: center; top: 195px; font-size: 38px; }
  .card--back .brand-name  { left: 170px; top: 63px; font-size: 38px; }

  .tagline { position: absolute; white-space: nowrap; line-height: 1; }
  .card--front .tagline { left: 0; width: 100%; text-align: center; top: 238px; font-size: 20px; }
  .card--back .tagline  { left: 171px; top: 110px; font-size: 19px; font-family: "Arimo", sans-serif; }

  .services-band {
    position: absolute; left: 0; top: 302px; width: 100%; height: 74px;
    background: linear-gradient(90deg, var(--red-dark) 0%, var(--red) 55%, var(--red-mid) 100%);
  }
  .services-pill {
    position: absolute; left: 219px; top: 288px; width: 186px; height: 27px;
    border-radius: 14px; background: linear-gradient(#ffffff, #dcdcdc);
    border: 2px solid #3a5fae;
    color: var(--navy-text); font-weight: 700; font-size: 16px; letter-spacing: 2px;
    text-align: center; line-height: 23px;
  }
  .services-text {
    position: absolute; left: 0; top: 318px; width: 100%;
    text-align: center; font-size: 15.5px; line-height: 21px; color: #f4e9e9;
  }

  .person-name { position: absolute; left: 30px; top: 200px; font-size: 24px; font-weight: 600; line-height: 1.2; }
  .qualifications { position: absolute; left: 30px; top: 232px; font-size: 15px; font-style: italic; line-height: 21px; color: #e6ecf7; }

  .contact-list { position: absolute; left: 344px; top: 203px; list-style: none; }
  .contact-list li { display: flex; align-items: center; height: 23px; font-size: 15.5px; }
  .contact-list svg { width: 16px; height: 16px; margin-right: 11px; fill: #dfe7f5; }

  .footer-shape { position: absolute; left: 0; top: 0; width: 618px; height: 374px; }
  .footer-left { position: absolute; left: 30px; top: 326px; font-family: "Arimo", sans-serif; font-size: 16px; line-height: 1.2; }
  .footer-right { position: absolute; left: 282px; top: 339px; font-family: "Arimo", sans-serif; font-size: 16px; line-height: 1.2; }
</style>
</head>
<body>

<section class="card card--front" aria-label="Front of card">
  <div class="brand-disc"></div>
  <h1 class="brand-name">JOLLY PAWS</h1>
  <p class="tagline">HAPPY DOGS, HAPPY OWNERS</p>
  <div class="services-band"></div>
  <div class="services-pill">SERVICES</div>
  <p class="services-text">Providing individual coaching strategies to create happy,<br>healthy and social canine companions</p>
</section>

<section class="card card--back" aria-label="Back of card">
  <svg class="footer-shape" viewBox="0 0 618 374" aria-hidden="true">
    <defs>
      <linearGradient id="footerRed" x1="0" x2="1" y1="0" y2="0">
        <stop offset="0" stop-color="#8e1c20"/>
        <stop offset="0.6" stop-color="#cf171e"/>
        <stop offset="1" stop-color="#b5181e"/>
      </linearGradient>
      <linearGradient id="footerCream" x1="0" x2="1" y1="0" y2="0">
        <stop offset="0" stop-color="#d9cfb0"/>
        <stop offset="0.5" stop-color="#f3eddb"/>
        <stop offset="1" stop-color="#c9bd98"/>
      </linearGradient>
    </defs>
    <path d="M0 360 H270 L258 374 H0 Z" fill="url(#footerCream)"/>
    <path d="M283 328 H618 V374 H254 Z" fill="url(#footerRed)"/>
  </svg>

  <div class="brand-disc"></div>
  <h2 class="brand-name">JOLLY PAWS</h2>
  <p class="tagline">HAPPY DOGS, HAPPY OWNERS</p>

  <h3 class="person-name">Denise Carvell</h3>
  <p class="qualifications">Qualified in Dog Behavioural Training,<br>Natural Animal Healthcare and<br>Animal Health Science</p>

  <ul class="contact-list">
    <li><svg viewBox="0 0 16 16"><path d="M4 1h8v14H4zM5.5 2.5v4h5v-4zM5.5 8h1.5v1.3H5.5zm2.3 0h1.5v1.3H7.8zm2.2 0h1.5v1.3H10zM5.5 10.2h1.5v1.3H5.5zm2.3 0h1.5v1.3H7.8zm2.2 0h1.5v1.3H10zM5.5 12.4h1.5v1.3H5.5zm2.3 0h1.5v1.3H7.8zm2.2 0h1.5v1.3H10z" fill-rule="evenodd"/></svg>0412 860 375</li>
    <li><svg viewBox="0 0 16 16"><path d="M1 4h14v9H1z"/><path d="M1 4l7 5 7-5" fill="none" stroke="#2a5fb0" stroke-width="1"/></svg>jollypaws1@mailbox.com</li>
  </ul>

  <p class="footer-left">Promoting Communication</p>
  <p class="footer-right">Connection between dogs &amp; their families</p>
</section>

</body>
</html>
```